Business Card - connecting 2 souls and beggining the journey of self discovery

Logo on the front
with tag line

On the back list of services and contact details

Seminars
workshops
Coaching
podcasts

Darren Whitlow
Health & Wellbeing Life Coach
0491 372 615
darren@brightcoreliving.example
brightcoreliving.example

Industry/Entity Type

Life Coaching

Contact Information for Business Card

I like the use of colour from the logo to be used. I'm not a fan of white.

Requirements
Must have
• My tagline: The journey home starts with you
Nice to have
• Use of colour that is in the Brightcore Living logo

```html
<!DOCTYPE html>
<html lang="en">
<head>
<meta charset="utf-8">
<title>Brightcore Living – Business Card</title>
<link rel="stylesheet" href="https://fonts.googleapis.com/css2?family=Poppins:wght@300;500;600&display=swap">
<style>
  :root {
    --canvas: #767272;
    --card: #ffffff;
    --ink: #222222;
    --night: #000000;
    --blue: #1a6fb3;
    --blue-deep: #0b5ea6;
    --blue-shade: #2c6ea8;
    --service-blue: #1760a8;
    --brand-green: #4fae55;
    --white: #ffffff;
  }
  * { margin: 0; padding: 0; box-sizing: border-box; }
  html, body {
    width: 1200px; height: 1200px; overflow: hidden;
    background: var(--canvas);
    font-family: "Poppins", sans-serif;
  }
  .canvas { position: relative; width: 1200px; height: 1200px; }
  .card {
    position: absolute; left: 120px; width: 960px; height: 550px;
    background: var(--card); overflow: hidden;
  }
  .card--back { top: 33px; }
  .card--front { top: 617px; }
  .card-shapes { position: absolute; inset: 0; }

  /* back card */
  .brand { position: absolute; left: 79px; top: 62px; width: 300px; text-align: center; }
  .brand-dot {
    width: 124px; height: 124px; border-radius: 50%;
    background: var(--brand-green); margin: 0 auto 12px;
  }
  .brand-name { font-weight: 600; font-size: 26px; color: var(--ink); }
  .tagline { position: absolute; left: 4px; top: 298px; width: 450px; text-align: center;
    font-weight: 500; font-size: 24px; color: var(--ink); white-space: nowrap; }
  .services { position: absolute; left: 62px; top: 374px; width: 340px;
    display: grid; grid-template-columns: 198px 1fr; row-gap: 14px; list-style: none; }
  .services li { font-weight: 500; font-size: 25px; color: var(--service-blue); }
  .services li::before { content: "•"; margin-right: 10px; }

  .identity { position: absolute; left: 474px; top: 90px; width: 486px; text-align: center; color: var(--white); padding-left: 20px; }
  .identity-name { font-weight: 600; font-size: 40px; line-height: 1.1; }
  .identity-role { font-weight: 300; font-size: 21px; margin-top: 2px; }

  .contacts { position: absolute; left: 530px; top: 324px; list-style: none; }
  .contacts li { display: flex; align-items: center; height: 38px; margin-bottom: 32px;
    color: var(--white); font-weight: 500; font-size: 19px; white-space: nowrap; }
  .contacts svg { width: 38px; height: 38px; margin-right: 20px; flex: none; }

  /* front card */
  .front-brand { position: absolute; left: 0; right: 0; top: 120px; text-align: center; }
  .front-brand .brand-dot { width: 150px; height: 150px; }
  .front-brand .brand-name { font-size: 32px; }
  .front-tagline { position: absolute; left: 0; right: 0; top: 372px; text-align: center;
    font-weight: 500; font-size: 36px; color: var(--ink); }
</style>
</head>
<body>
<div class="canvas">

  <section class="card card--back">
    <svg class="card-shapes" viewBox="0 0 960 550" aria-hidden="true">
      <defs>
        <linearGradient id="bandGrad" x1="0" x2="1">
          <stop offset="0" stop-color="#0b63ad"/>
          <stop offset="1" stop-color="#1a73b8"/>
        </linearGradient>
      </defs>
      <polygon points="672,0 960,0 960,550 415,550" fill="var(--night)"/>
      <polygon points="474,187 584,187 551,256" fill="var(--blue-shade)"/>
      <rect x="474" y="80" width="486" height="107" fill="url(#bandGrad)"/>
    </svg>

    <div class="brand">
      <div class="brand-dot"></div>
      <div class="brand-name">Brightcore Living</div>
    </div>
    <p class="tagline">The journey home starts with you</p>
    <ul class="services">
      <li>Seminars</li><li>Coaching</li>
      <li>Workshops</li><li>Podcasts</li>
    </ul>

    <div class="identity">
      <div class="identity-name">Darren Whitlow</div>
      <div class="identity-role">Health &amp; Wellbeing Life Coach</div>
    </div>

    <ul class="contacts">
      <li>
        <svg viewBox="0 0 38 38" aria-hidden="true"><circle cx="19" cy="19" r="19" fill="var(--blue)"/>
          <path d="M13 10c1-1 2-1 3 0l2 3c.5 1 0 2-1 2.5-.5.5 0 2 1.5 3.5s3 2 3.5 1.5c.5-1 1.5-1.5 2.5-1l3 2c1 1 1 2 0 3-2 2-5 2-9-2s-5-9-5-12z" fill="var(--white)"/></svg>
        0491 372 615
      </li>
      <li>
        <svg viewBox="0 0 38 38" aria-hidden="true"><circle cx="19" cy="19" r="19" fill="var(--blue)"/>
          <rect x="10" y="12.5" width="18" height="13" fill="var(--white)"/>
          <path d="M10 12.5l9 7 9-7M10 25.5l6.5-6M28 25.5l-6.5-6" stroke="var(--blue)" stroke-width="1.5" fill="none"/></svg>
        darren@brightcoreliving.example
      </li>
      <li>
        <svg viewBox="0 0 38 38" aria-hidden="true"><circle cx="19" cy="19" r="19" fill="var(--blue)"/>
          <circle cx="19" cy="19" r="9" fill="none" stroke="var(--white)" stroke-width="2"/>
          <ellipse cx="19" cy="19" rx="4" ry="9" fill="none" stroke="var(--white)" stroke-width="1.6"/>
          <path d="M10 19h18" stroke="var(--white)" stroke-width="1.6"/></svg>
        www.brightcoreliving.example
      </li>
    </ul>
  </section>

  <section class="card card--front">
    <svg class="card-shapes" viewBox="0 0 960 550" aria-hidden="true">
      <rect x="0" y="494" width="960" height="22" fill="var(--blue-deep)"/>
      <rect x="0" y="516" width="960" height="4" fill="var(--white)"/>
      <rect x="0" y="520" width="960" height="30" fill="var(--blue-deep)"/>
    </svg>
    <div class="front-brand">
      <div class="brand-dot"></div>
      <div class="brand-name">Brightcore Living</div>
    </div>
    <p class="front-tagline">The journey home starts with you</p>
  </section>

</div>
</body>
</html>
```